Brody's Lot Grading & Trenching

I would like to have business cards created for my land clearing company. We have excavators, skid steers, dump trucks, tractor trailer dump trailers, forestry mulchers along with all size tractors for pasture restoration and arena builds.

Target Market(s)

Both commercial and residential clients

Contact Information for Business Card

Name, phone number, email and website

Colors

Designer to choose colors to be used in the design.

```html
<!DOCTYPE html>
<html lang="en">
<head>
<meta charset="utf-8">
<title>Brody's Lot Grading &amp; Trenching – Business Card</title>
<link rel="stylesheet" href="https://fonts.googleapis.com/css2?family=Rubik:ital,wght@0,400;0,500;0,600;0,700;1,400;1,500;1,600&display=swap">
<style>
  :root {
    --ink: #1b1b1b;
    --cream: #fbefd8;
    --yellow: #f9cc0e;
    --steel: #b5b5b7;
    --white: #ffffff;
    --page: #ececec;
  }
  * { margin: 0; padding: 0; box-sizing: border-box; }
  html, body { width: 1200px; height: 1092px; overflow: hidden; background: var(--page); }
  body { font-family: "Rubik", sans-serif; color: var(--ink); position: relative; }

  .card {
    position: absolute; left: 160px; width: 880px; height: 503px;
    background: var(--cream); overflow: hidden;
    box-shadow: 0 6px 18px rgba(0,0,0,.18);
  }
  .card-front { top: 30px; }
  .card-back { top: 559px; }
  .card-shapes { position: absolute; inset: 0; }

  /* front */
  .contact-block { position: absolute; left: 56px; top: 64px; width: 330px; color: var(--white); }
  .person-name { font-size: 36px; font-weight: 600; font-style: italic; color: var(--yellow); }
  .person-role { font-size: 19px; font-style: italic; margin-top: 2px; }
  .contact-list { list-style: none; margin-top: 120px; font-size: 18px; line-height: 30px; }
  .contact-list li { display: flex; align-items: center; gap: 12px; white-space: nowrap; }
  .contact-list svg { width: 18px; height: 18px; fill: var(--yellow); flex: none; }
  .company-line { margin-top: 30px; font-size: 17px; font-style: italic; color: var(--yellow); white-space: nowrap; }
  .location-line { font-size: 17px; font-style: italic; margin-top: 2px; }

  .brand { position: absolute; display: flex; align-items: center; gap: 16px; }
  .brand-mark { width: 54px; height: 54px; border-radius: 50%; background: var(--yellow); flex: none; }
  .brand-name { font-size: 28px; font-weight: 600; line-height: 1.15; color: var(--ink); }
  .card-front .brand { left: 520px; top: 210px; width: 330px; }
  .card-back .brand { right: 56px; top: 70px; width: 380px; flex-direction: row-reverse; text-align: right; }

  /* back */
  .service-list { position: absolute; list-style: none; font-size: 16px; font-weight: 600; line-height: 24px; }
  .service-list li { display: flex; align-items: center; gap: 10px; white-space: nowrap; }
  .service-list li::before { content: ""; width: 7px; height: 7px; border-radius: 50%; background: var(--ink); }
  .services-a { left: 60px; top: 256px; }
  .services-b { left: 340px; top: 296px; }
  .services-c { left: 620px; top: 336px; }
</style>
</head>
<body>

<section class="card card-front" aria-label="Business card front">
  <svg class="card-shapes" viewBox="0 0 880 503" aria-hidden="true">
    <polygon points="0,0 510,0 390,503 0,503" fill="var(--ink)"/>
    <polygon points="510,0 536,0 476,251 450,251" fill="var(--steel)"/>
    <polygon points="450,251 476,251 416,503 390,503" fill="var(--yellow)"/>
  </svg>

  <div class="contact-block">
    <div class="person-name">Cole Harper</div>
    <div class="person-role">owner</div>
    <ul class="contact-list">
      <li><svg viewBox="0 0 24 24"><path d="M6.6 10.8a15.1 15.1 0 0 0 6.6 6.6l2.2-2.2a1 1 0 0 1 1-.25 11.4 11.4 0 0 0 3.6.57 1 1 0 0 1 1 1V20a1 1 0 0 1-1 1A17 17 0 0 1 3 4a1 1 0 0 1 1-1h3.5a1 1 0 0 1 1 1c0 1.25.2 2.45.57 3.57a1 1 0 0 1-.25 1z"/></svg>(555) 014-2290</li>
      <li><svg viewBox="0 0 24 24"><path d="M2 5h20v2l-10 6L2 7zM2 9l10 6 10-6v10H2z"/></svg>info@brodyslotgrading.com</li>
      <li><svg viewBox="0 0 24 24"><circle cx="12" cy="12" r="10" fill="none" stroke="var(--yellow)" stroke-width="2"/><path d="M2 12h20M12 2c3 3 3 17 0 20M12 2c-3 3-3 17 0 20" fill="none" stroke="var(--yellow)" stroke-width="2"/></svg>www.brodyslotgrading.com</li>
    </ul>
    <div class="company-line">Brody's Lot Grading &amp; Trenching, LLC</div>
    <div class="location-line">Pine Hollow</div>
  </div>

  <div class="brand">
    <span class="brand-mark"></span>
    <span class="brand-name">Brody's Lot Grading &amp; Trenching, LLC</span>
  </div>
</section>

<section class="card card-back" aria-label="Business card back">
  <svg class="card-shapes" viewBox="0 0 880 503" aria-hidden="true">
    <rect x="0" y="208" width="560" height="14" fill="var(--steel)"/>
    <rect x="560" y="208" width="320" height="14" fill="var(--ink)"/>
    <rect x="0" y="222" width="880" height="281" fill="var(--yellow)"/>
  </svg>

  <div class="brand">
    <span class="brand-mark"></span>
    <span class="brand-name">Brody's Lot Grading &amp; Trenching, LLC</span>
  </div>

  <ul class="service-list services-a">
    <li>Excavation Services</li>
    <li>Site Clearing</li>
    <li>Land Clearing</li>
    <li>Demolition Services</li>
    <li>Bobcat Services</li>
    <li>Shoring</li>
  </ul>
  <ul class="service-list services-b">
    <li>Land Demolition</li>
    <li>Grading Service</li>
    <li>Regrading</li>
    <li>Resloping</li>
    <li>Site Preparation</li>
    <li>Building Site Preparation</li>
  </ul>
  <ul class="service-list services-c">
    <li>Land Site Preparation</li>
    <li>Construction Demolition</li>
    <li>Forestry Mulching</li>
    <li>Pasture Reseeding</li>
    <li>Build Arenas</li>
    <li>Pasture Stump Removal</li>
  </ul>
</section>

</body>
</html>
```